Irrigation Business needs their business cards modernised and revamped

I would like to keep my current logo, colours and revamp the format of the card.

I would like the card to be clean yet important.

Im not sure if you include texture but i would like the named logo to be indented into the card etc.

show me something alive and free something thats clinical to the point yet has a feel of achievement. i would like people to go nice card.

Target Market(s)

high end clients, corporate, sports field manger, the guys that make the decisions

Industry/Entity Type

Business

Contact Information for Business Card

nformation to be included

Dean Harlow (Director)
0487305526
dean@kolvat.biz
www.kestonfieldworks.com

instagram logo
google logo
facebook logo

Colors

Designer to choose colors to be used in the design.

Requirements
Nice to have
• indentations a really nice feel to the card good texture

```html
<!DOCTYPE html>
<html lang="en">
<head>
<meta charset="utf-8">
<title>Keston Fieldworks – Business Card</title>
<link href="https://fonts.googleapis.com/css2?family=Open+Sans:wght@400;600;700;800&display=swap" rel="stylesheet">
<style>
  :root {
    --stage: #2a2a2c;
    --card-white: #f7f7f5;
    --brand-blue: #2f6cb4;
    --brand-sky: #38a8dc;
    --ink-white: #ffffff;
  }
  * { margin: 0; padding: 0; box-sizing: border-box; }
  html, body {
    width: 1200px; height: 900px; overflow: hidden;
    background: var(--stage);
    font-family: "Open Sans", Arial, sans-serif;
  }
  .stage {
    position: relative; width: 1200px; height: 900px;
    display: flex; flex-direction: column; align-items: center; justify-content: center; gap: 36px;
  }
  .card {
    position: relative; width: 630px; height: 360px; overflow: hidden;
    box-shadow: 0 12px 30px rgba(0,0,0,.45);
  }
  /* front */
  .card-front {
    background: var(--card-white);
    display: flex; flex-direction: column; align-items: center; justify-content: center;
  }
  .brand-lockup { display: flex; align-items: center; gap: 18px; }
  .brand-dot { width: 62px; height: 62px; border-radius: 50%; background: var(--brand-sky); }
  .brand-name {
    color: var(--brand-blue); font-weight: 800; font-size: 38px;
    letter-spacing: .5px; text-transform: uppercase; line-height: 1;
  }
  .social-row { display: flex; gap: 8px; margin-top: 22px; }
  .social-dot { width: 18px; height: 18px; border-radius: 50%; background: var(--brand-blue); }
  /* back */
  .card-back { background: var(--card-white); }
  .back-band {
    position: absolute; left: 0; top: 0; bottom: 0; width: 445px;
    background: var(--brand-blue);
  }
  .back-emblem { position: absolute; left: 335px; top: 20px; }
  .contact {
    position: absolute; left: 44px; bottom: 44px; color: var(--ink-white);
  }
  .contact-name { font-weight: 700; font-size: 18px; text-transform: uppercase; letter-spacing: .3px; }
  .contact-role { font-size: 15px; text-transform: uppercase; margin-bottom: 18px; }
  .contact-list { list-style: none; }
  .contact-list li { display: flex; align-items: center; gap: 10px; font-size: 15px; line-height: 24px; }
  .contact-list svg { width: 13px; height: 13px; fill: var(--ink-white); flex: none; }
</style>
</head>
<body>
<main class="stage">
  <section class="card card-front">
    <div class="brand-lockup">
      <span class="brand-dot"></span>
      <span class="brand-name">Keston Fieldworks</span>
    </div>
    <div class="social-row">
      <span class="social-dot"></span>
      <span class="social-dot"></span>
      <span class="social-dot"></span>
    </div>
  </section>

  <section class="card card-back">
    <div class="back-band"></div>
    <svg class="back-emblem" width="320" height="320" viewBox="0 0 320 320" aria-hidden="true">
      <circle cx="160" cy="160" r="156" fill="#ffffff"/>
      <circle cx="160" cy="160" r="140" fill="#38a8dc"/>
    </svg>
    <div class="contact">
      <p class="contact-name">Dean Harlow</p>
      <p class="contact-role">Director</p>
      <ul class="contact-list">
        <li><svg viewBox="0 0 16 16"><path d="M3 1h3l1.5 4-2 1.2a9 9 0 0 0 4.3 4.3L11 8.5l4 1.5v3a2 2 0 0 1-2 2A12 12 0 0 1 1 3a2 2 0 0 1 2-2z"/></svg>0487305526</li>
        <li><svg viewBox="0 0 16 16"><path d="M1 3h14v10H1z M1 3l7 6 7-6" fill="none" stroke="#fff" stroke-width="1.6"/></svg>dean@kolvat.biz</li>
        <li><svg viewBox="0 0 16 16"><circle cx="8" cy="8" r="6.5" fill="none" stroke="#fff" stroke-width="1.6"/><path d="M1.5 8h13M8 1.5c-3 3.5-3 9.5 0 13M8 1.5c3 3.5 3 9.5 0 13" fill="none" stroke="#fff" stroke-width="1.2"/></svg>kestonfieldworks.com</li>
      </ul>
    </div>
  </section>
</main>
</body>
</html>
```